Pet Sitting Business Card

Would like a business card designed for my new pet sitting business
Card needs to match with logo design.
Blue and Orange are the theme colours.

Simple yet sophisticated design

company name:- MEADOWLARK PET CARE
Dana Kovich
Owner
0452716093
dana@meadowlarkpetcare.com.au
www.meadowlarkpetcare.com.au

I'm going to close my deadline early. I will be picking a winner by the 10th of May. Please submit designs before then.
thank you

Target Market(s)

All types of professional pet lovers wishing to have their pet looked after

Industry/Entity Type

Pet

Requirements
Must have
• Logo design
Blue and orange

```html
<!DOCTYPE html>
<html lang="en">
<head>
<meta charset="utf-8">
<title>Meadowlark Pet Care – Business Card</title>
<link href="https://fonts.googleapis.com/css2?family=Exo+2:wght@400;500;600&family=Cinzel:wght@700&display=swap" rel="stylesheet">
<style>
  :root {
    --page-bg: #e9eaec;
    --card-light: #ffffff;
    --card-shade: #dcdddf;
    --brand-blue: #2f95ea;
    --brand-blue-light: #4fc0e0;
    --brand-orange: #ef8a2a;
    --ink-dark: #3a3a3a;
    --ink-white: #ffffff;
  }
  * { box-sizing: border-box; margin: 0; padding: 0; }
  html, body {
    width: 1200px; height: 869px; overflow: hidden;
    background: var(--page-bg);
    font-family: "Exo 2", "Trebuchet MS", sans-serif;
  }
  .sheet {
    width: 1200px; height: 869px;
    display: flex; align-items: center; justify-content: center; gap: 36px;
  }
  .card {
    position: relative;
    width: 560px; height: 320px;
    border-radius: 22px;
    overflow: hidden;
    background: radial-gradient(ellipse at 45% 55%, var(--card-light) 0%, var(--card-shade) 100%);
    box-shadow: 0 6px 22px rgba(0,0,0,0.18);
  }
  .card-shapes { position: absolute; inset: 0; width: 100%; height: 100%; }

  /* front */
  .contact-list {
    position: absolute; left: 26px; top: 24px;
    list-style: none; color: var(--ink-white);
    font-size: 14px; line-height: 1.25;
  }
  .contact-item { display: flex; align-items: flex-start; gap: 9px; margin-bottom: 9px; }
  .contact-icon { width: 18px; height: 18px; flex: none; }
  .contact-address { max-width: 170px; }

  .brand-mark {
    position: absolute; right: 36px; top: 150px;
    display: flex; align-items: center; gap: 10px;
  }
  .brand-dot { width: 22px; height: 22px; border-radius: 50%; background: var(--brand-orange); }
  .brand-name {
    font-family: "Cinzel", Georgia, serif; font-weight: 700;
    color: var(--brand-blue); font-size: 22px; letter-spacing: 0.5px;
    text-align: right; line-height: 1.1;
  }
  .holder { position: absolute; right: 36px; bottom: 28px; text-align: right; }
  .holder-name { color: var(--brand-blue); font-size: 21px; font-weight: 500; letter-spacing: 1.5px; }
  .holder-role { color: var(--ink-dark); font-size: 14px; font-weight: 600; letter-spacing: 1.8px; margin-top: 3px; }

  /* back */
  .card-back .brand-mark {
    position: absolute; inset: 0; right: auto; top: auto;
    width: 100%; height: 100%; justify-content: center; flex-direction: column; gap: 14px;
  }
  .card-back .brand-dot { width: 34px; height: 34px; }
  .card-back .brand-name { font-size: 34px; text-align: center; }
</style>
</head>
<body>
<main class="sheet">

  <section class="card card-front" aria-label="Business card front">
    <svg class="card-shapes" viewBox="0 0 560 320" preserveAspectRatio="none" aria-hidden="true">
      <defs>
        <linearGradient id="bandBlue" x1="0" y1="1" x2="1" y2="0">
          <stop offset="0" stop-color="#2f95ea"/>
          <stop offset="0.55" stop-color="#4fc0e0"/>
          <stop offset="1" stop-color="#2f95ea"/>
        </linearGradient>
      </defs>
      <path d="M0,0 H560 V70 C420,70 300,110 240,180 C180,250 90,290 0,305 Z" fill="url(#bandBlue)"/>
      <path d="M262,168 C330,104 440,86 560,88 V110 C440,106 340,122 262,168 Z" fill="#ef8a2a"/>
    </svg>

    <ul class="contact-list">
      <li class="contact-item">
        <svg class="contact-icon" viewBox="0 0 18 18" aria-hidden="true"><circle cx="9" cy="9" r="9" fill="#fff"/><path d="M6 4.5c1 0 1.4 2 1 2.5l-.6.6c.5 1.2 1.4 2.1 2.6 2.6l.6-.6c.5-.4 2.5 0 2.5 1 0 1-1 2-2 1.9C7 12.2 5.7 10.9 5 8.1 4.2 6 5 4.5 6 4.5z" fill="#2f95ea"/></svg>
        <span>0452716093</span>
      </li>
      <li class="contact-item">
        <svg class="contact-icon" viewBox="0 0 18 18" aria-hidden="true"><circle cx="9" cy="9" r="9" fill="#fff"/><rect x="6" y="3.5" width="6" height="11" rx="1.2" fill="#2f95ea"/><rect x="7" y="5" width="4" height="6.5" fill="#fff"/></svg>
        <span>0452716093</span>
      </li>
      <li class="contact-item">
        <svg class="contact-icon" viewBox="0 0 18 18" aria-hidden="true"><circle cx="9" cy="9" r="9" fill="#fff"/><rect x="4" y="5.5" width="10" height="7" rx="1" fill="#2f95ea"/><path d="M4.5 6l4.5 3.5L13.5 6" stroke="#fff" stroke-width="1" fill="none"/></svg>
        <span>dana@meadowlarkpetcare.com.au</span>
      </li>
      <li class="contact-item">
        <svg class="contact-icon" viewBox="0 0 18 18" aria-hidden="true"><circle cx="9" cy="9" r="9" fill="#fff"/><circle cx="9" cy="9" r="5" fill="none" stroke="#2f95ea" stroke-width="1.3"/><path d="M4 9h10M9 4c-2.5 3-2.5 7 0 10M9 4c2.5 3 2.5 7 0 10" stroke="#2f95ea" stroke-width="1" fill="none"/></svg>
        <span>www.meadowlarkpetcare.com.au</span>
      </li>
      <li class="contact-item">
        <svg class="contact-icon" viewBox="0 0 18 18" aria-hidden="true"><circle cx="9" cy="9" r="9" fill="#fff"/><path d="M9 3.5a3.6 3.6 0 0 1 3.6 3.6C12.6 10 9 14.5 9 14.5S5.4 10 5.4 7.1A3.6 3.6 0 0 1 9 3.5z" fill="#2f95ea"/><circle cx="9" cy="7.2" r="1.3" fill="#fff"/></svg>
        <span class="contact-address">27 Wattle Grove, Level 2, Bayside Road</span>
      </li>
    </ul>

    <div class="brand-mark">
      <span class="brand-dot" aria-hidden="true"></span>
      <span class="brand-name">MEADOWLARK<br>PET CARE</span>
    </div>

    <div class="holder">
      <p class="holder-name">DANA KOVICH</p>
      <p class="holder-role">OWNER</p>
    </div>
  </section>

  <section class="card card-back" aria-label="Business card back">
    <div class="brand-mark">
      <span class="brand-dot" aria-hidden="true"></span>
      <span class="brand-name">MEADOWLARK<br>PET CARE</span>
    </div>
  </section>

</main>
</body>
</html>
```